Belmont Ridge Business Card Design Project

We have recently rebranded and would like to design new business cards that incorporate the corporate logo - double sided cards with corporate logo on one side and contact details on the other

Target Market(s)

Sophisticated and high net worth investors and finance industry professionals

Industry/Entity Type

Funds Management

Contact Information for Business Card

The card should prominently feature the company name and logo. Other details will be standard contact details for each staff member - name, address, phone, email, website

Colors
0054AA
0677BA
7BADD7
CADEEF
E8F1F8

Requirements
Must have
• Double-sided design with one side prominently featuring the corporate logo and the other side with all standard contact details

```html
<!DOCTYPE html>
<html lang="en">
<head>
<meta charset="utf-8">
<title>Belmont Ridge Business Card</title>
<link href="https://fonts.googleapis.com/css2?family=Cinzel:wght@500;600&family=Libre+Baskerville:wght@700&family=Arimo:wght@400&display=swap" rel="stylesheet">
<style>
  :root {
    --navy: #174675;
    --ink: #2b2b2b;
    --paper: #ffffff;
    --backdrop: #9a9a9a;
  }
  * { margin: 0; padding: 0; box-sizing: border-box; }
  html, body { width: 1200px; height: 1059px; overflow: hidden; }
  body { background: var(--backdrop); position: relative; font-family: "Arimo", Arial, sans-serif; }

  .card { position: absolute; border-radius: 21px; overflow: hidden; }

  .card-front { left: 256px; top: 89px; width: 688px; height: 391px; background: var(--paper); }
  .brand-wordmark {
    position: absolute; right: 35px; top: 96px;
    font-family: "Cinzel", serif; font-weight: 600; font-size: 38px;
    color: var(--navy); letter-spacing: 0.5px; white-space: nowrap;
  }
  .person { position: absolute; left: 35px; top: 186px; }
  .person-name {
    font-family: "Libre Baskerville", serif; font-weight: 700; font-size: 21px;
    color: var(--navy); letter-spacing: 0.3px; line-height: 1.1;
  }
  .person-title { font-size: 16px; color: var(--ink); margin-top: 2px; }
  .divider { position: absolute; left: 35px; right: 35px; top: 251px; height: 1px; background: var(--navy); }

  .contact-list { position: absolute; left: 35px; top: 275px; list-style: none; }
  .contact-list li {
    display: flex; align-items: center; gap: 8px;
    font-size: 17px; color: var(--ink); height: 28px;
  }
  .contact-list svg { width: 13px; height: 13px; fill: var(--navy); flex: none; }

  .address {
    position: absolute; right: 35px; top: 309px; text-align: right;
    font-size: 17px; color: var(--ink); line-height: 22px; font-style: normal;
  }

  .card-back {
    left: 253px; top: 569px; width: 695px; height: 394px; background: var(--navy);
    display: flex; align-items: center; justify-content: center;
  }
  .brand-wordmark-large {
    font-family: "Cinzel", serif; font-weight: 600; font-size: 54px;
    color: var(--paper); letter-spacing: 1px; white-space: nowrap;
  }
</style>
</head>
<body>
  <section class="card card-front" aria-label="Business card front">
    <div class="brand-wordmark">Belmont Ridge</div>

    <div class="person">
      <div class="person-name">DANIEL HALE</div>
      <div class="person-title">CEO/Founder</div>
    </div>

    <div class="divider"></div>

    <ul class="contact-list">
      <li>
        <svg viewBox="0 0 24 24" aria-hidden="true"><path d="M6.6 10.8a15.1 15.1 0 0 0 6.6 6.6l2.2-2.2a1 1 0 0 1 1-.25 11.4 11.4 0 0 0 3.6.57 1 1 0 0 1 1 1V20a1 1 0 0 1-1 1A17 17 0 0 1 3 4a1 1 0 0 1 1-1h3.5a1 1 0 0 1 1 1c0 1.25.2 2.45.57 3.57a1 1 0 0 1-.25 1z"/></svg>
        (555) 410-7788
      </li>
      <li>
        <svg viewBox="0 0 24 24" aria-hidden="true"><path d="M2 5h20v2.2l-10 6-10-6z M2 9.5l10 6 10-6V19H2z"/></svg>
        info@belmontridge.com
      </li>
      <li>
        <svg viewBox="0 0 24 24" aria-hidden="true"><path d="M12 2a10 10 0 1 0 0 20 10 10 0 0 0 0-20zm0 2c.9 1.1 1.6 2.6 2 4h-4c.4-1.4 1.1-2.9 2-4zM4.3 14a8 8 0 0 1 0-4h3.3a16 16 0 0 0 0 4zm.9 2h3a14 14 0 0 0 1.3 3.4A8 8 0 0 1 5.2 16zm3-8h-3a8 8 0 0 1 4.3-3.4A14 14 0 0 0 8.2 8zM12 20c-.9-1.1-1.6-2.6-2-4h4c-.4 1.4-1.1 2.9-2 4zm2.3-6H9.7a14 14 0 0 1 0-4h4.6a14 14 0 0 1 0 4zm.2 5.4a14 14 0 0 0 1.3-3.4h3a8 8 0 0 1-4.3 3.4zm1.9-5.4a16 16 0 0 0 0-4h3.3a8 8 0 0 1 0 4zm-.6-6a14 14 0 0 0-1.3-3.4A8 8 0 0 1 18.8 8z"/></svg>
        www.belmontridge.com
      </li>
    </ul>

    <address class="address">
      Po Box 2190 Harbour Lane<br>
      Westfield AB 3307
    </address>
  </section>

  <section class="card card-back" aria-label="Business card back">
    <div class="brand-wordmark-large">Belmont Ridge</div>
  </section>
</body>
</html>
```